Veltrova Website

I would like to have a revised web site for Veltrova. Veltrova is two companies - Veltrova Insurance Company and Veltrova Re Intermediaries. The logos are set, the site content is set, but the flow and look of the web site is clunky.

We do need a landing page that allows someone to choose either company. The one we have is very basic.

Current photos are not required, just ones we used.

www.veltrova-example.com is the site.

Target Market(s)

Business professionals (insurance)

Industry/Entity Type

Insurance

Requirements
Must have
• Veltrova Insurance Company
• Veltrova Re Intermediaries
• Current logos

```html
<!DOCTYPE html>
<html lang="en">
<head>
<meta charset="utf-8">
<title>Veltrova Re Intermediaries</title>
<link rel="stylesheet" href="https://fonts.googleapis.com/css2?family=Hind:wght@300;400;500;600&display=swap">
<style>
  :root {
    --brand-red: #d71f26;
    --text-dark: #3a3a3a;
    --text-body: #6b6b6b;
    --page-bg: #f8f8f8;
    --footer-bg: #efefef;
    --card-border: #e2e2e2;
    --white: #ffffff;
    --tw-blue: #5fc3ec;
    --fb-blue: #3b5a9a;
  }
  * { box-sizing: border-box; margin: 0; padding: 0; }
  html, body { width: 1200px; height: 1170px; overflow: hidden; }
  body {
    position: relative;
    background: var(--page-bg);
    font-family: "Hind", sans-serif;
    color: var(--text-body);
  }
  .hero {
    position: absolute; left: 0; top: 0; width: 1200px; height: 472px;
    background: linear-gradient(180deg, #5e5aa0 0%, #8b7aa8 22%, #d2a878 42%, #6c5a55 62%, #3f3a3e 76%, #6e6b78 88%, #8e8a96 100%);
  }
  .slider-dots {
    position: absolute; top: 421px; left: 562px; display: flex; gap: 6px;
  }
  .slider-dots span {
    width: 14px; height: 14px; border-radius: 50%; background: var(--white);
  }
  .slider-dots span.is-active { background: var(--brand-red); }

  .site-header {
    position: absolute; left: 118px; top: 40px; width: 962px; height: 83px;
    background: var(--white);
    box-shadow: 0 8px 10px -4px rgba(0,0,0,0.45);
  }
  .brand {
    position: absolute; left: 22px; top: 24px;
    display: flex; align-items: center; gap: 8px;
    font-size: 22px; font-weight: 400; color: #2e3340; letter-spacing: 0.3px;
  }
  .brand-mark { width: 12px; height: 12px; border-radius: 50%; background: var(--brand-red); }
  .main-nav {
    position: absolute; right: 0; top: 0; height: 83px; display: flex;
  }
  .main-nav a {
    position: relative; display: block; padding: 30px 15px 0;
    font-size: 19px; font-weight: 300; color: var(--text-dark); text-decoration: none;
  }
  .main-nav a.nav-contact { padding-left: 24px; padding-right: 33px; }
  .main-nav a.is-current::before {
    content: ""; position: absolute; left: 0; right: 0; top: 0; height: 7px; background: var(--brand-red);
  }

  .section-title {
    position: absolute; color: var(--brand-red); font-weight: 500; font-size: 19px;
  }
  .services-title { left: 125px; top: 510px; }
  .service {
    position: absolute; top: 548px; width: 302px;
  }
  .service h3 {
    font-size: 14.5px; font-weight: 300; color: var(--text-dark); margin-left: -2px; height: 29px;
  }
  .service-frame {
    width: 302px; height: 193px; background: var(--white);
    border: 1px solid var(--card-border); padding: 6px;
  }
  .service-photo { width: 288px; height: 179px; }
  .photo-brokerage { background: linear-gradient(135deg, #e9e9ea, #a9aab0 50%, #3b3e48); }
  .photo-policy { background: linear-gradient(180deg, #7e9ab8 0%, #c5d0da 45%, #6f9a42 60%, #4c7a2c 100%); }
  .photo-claims { background: linear-gradient(135deg, #eef0ea, #d9b9a2 50%, #8fa1b3); }

  .welcome-title { left: 129px; top: 803px; }
  .welcome-sub {
    position: absolute; left: 131px; top: 846px;
    font-size: 14.5px; font-weight: 500; color: #5a5a5a;
  }
  .welcome-text {
    position: absolute; left: 130px; top: 870px; width: 939px;
    font-size: 14.5px; font-weight: 300; line-height: 24px; text-align: justify;
  }
  .welcome-text a { color: var(--brand-red); font-weight: 500; text-decoration: none; }

  .site-footer {
    position: absolute; left: 0; top: 1052px; width: 1200px; height: 118px; background: var(--footer-bg);
  }
  .footer-nav {
    position: absolute; left: 132px; top: 29px; font-size: 14.5px; font-weight: 300; color: var(--text-dark);
  }
  .footer-nav a { color: var(--text-dark); text-decoration: none; }
  .footer-nav .sep { margin: 0 8px; }
  .copyright {
    position: absolute; left: 132px; top: 66px; font-size: 14.5px; font-weight: 300; color: var(--text-dark);
  }
  .social { position: absolute; left: 991px; top: 50px; display: flex; gap: 8px; }
  .social span { width: 35px; height: 35px; border-radius: 50%; }
  .social .tw { background: var(--tw-blue); }
  .social .fb { background: var(--fb-blue); }
</style>
</head>
<body>
  <section class="hero" role="img" aria-label="City skyline across the water at sunset">
    <div class="slider-dots"><span class="is-active"></span><span></span><span></span><span></span></div>
  </section>

  <header class="site-header">
    <div class="brand"><span class="brand-mark"></span>VELTROVA RE</div>
    <nav class="main-nav">
      <a href="#" class="is-current">Home</a>
      <a href="#">About Us</a>
      <a href="#">Services</a>
      <a href="#" class="nav-contact">Contact Us</a>
    </nav>
  </header>

  <h2 class="section-title services-title">Our Services</h2>

  <article class="service" style="left:128px">
    <h3>Brokerage Services</h3>
    <div class="service-frame"><div class="service-photo photo-brokerage" role="img" aria-label="Business team reviewing a laptop together"></div></div>
  </article>
  <article class="service" style="left:448px">
    <h3>Policy Management Services</h3>
    <div class="service-frame"><div class="service-photo photo-policy" role="img" aria-label="Family standing in a field inside an outlined house shape"></div></div>
  </article>
  <article class="service" style="left:768px">
    <h3>Claims TPA</h3>
    <div class="service-frame"><div class="service-photo photo-claims" role="img" aria-label="Smiling family outdoors"></div></div>
  </article>

  <h2 class="section-title welcome-title">Welcome to Veltrova</h2>
  <p class="welcome-sub">Veltrova RE Intermediaries</p>
  <p class="welcome-text">We are a boutique reinsurance brokerage and advisory firm specialized in providing risk management, strategic consulting and risk transfer services to insurance companies, MGAs and producers alike. Established in 2013, Veltrova Re is a member of the industry leading Harwick Group of companies domiciled in Cedar Falls, Texas. Veltrova Re clearly differentiates itself within the marketplace by the unique opportunity provided to partners and clients. The experienced team brings an unmatched knowledge base of the personal lines (private passenger automobile) insurance and reinsurance marketplace. The team has successfully operated in every capacity; consulting services, independent agent, general agent, managing general agency, insurance company and reinsurance brokerage... <a href="#">Read More</a></p>

  <footer class="site-footer">
    <div class="footer-nav">
      <a href="#">Home</a><span class="sep">&nbsp;|</span><a href="#">About Us</a><span class="sep">|</span><a href="#">Services</a><span class="sep">|</span><a href="#">Contact Us</a>
    </div>
    <p class="copyright">Copyright ©2013&nbsp; Company Name &nbsp;&nbsp; - All rights reserved</p>
    <div class="social" aria-label="Social links"><span class="tw"></span><span class="fb"></span></div>
  </footer>
</body>
</html>
```